In need of a Wordpress website for a Water Sports Rental Company!

We are starting a new venture that provides a variety of rental equipment in the Cayman Islands. We are in need of a website where guests are able to book their rental gear during their stay in Cayman. We will also have an interactive map where guests can learn about off the beaten path activities to explore in here Cayman.

Our target market is middle/upper class, so we need a website that appeals to this group. We need our website to be clean, simple and easy to navigate. We need it to be highly visual and modern. We like the idea of the website having a tropical feel to it, we are very open to creative ideas that reflects this!

Must be designed in WordPress using the Velmora template I’ve provided.

You will find all instructions & the photos I want to use for this website on the following stashvo account:
- www.stashvo.com
- Username: hello@lumentrips.com
- Password: pelican7

All of the photos will need to be resized accordingly to be as small as possible without loosing resolution.

These are the tabs that will be used:
- Home Page
- Adventure Map
- Rental Gear
- Tours
- Photo Gallery
- Contact Us

Home Page
- You will find all the text and instructions for the home page in the word document named ‘Home Page’.

Adventure Map
- You will find all the text and instructions for the home page in the word document named ‘Adventure Map Content’
- There will also be a few 'guide' pages under this tab, which we will go in to detail with the winner.

Rentals
- You will find all the text and instructions for the Rentals page in the word document named ‘Rentals Content’

Tours
- This will just be a page saying ‘kayaking, snorkeling & Bioluminescence tours coming soon’.

Photo Gallery
- You will find the photos for this in our Stashvo.com Account

Contact Us
- Send us a Message – page will be similar to our other site http://lumentrips.com/contact/
- Phone: +1 (345) 555 0192
- Email: hello@tidalotterco.com

The big factors on who will have the winning design are:
- The background used
- The layout of the Home Page
- The animations at the top of the Rental Landing Page
- The overall clean, professional look to the website

If you have any questions, don't hesitate to ask.

We look forward to working with you all!!

Good luck!!

Target Market(s)

Middle/Upper Class on vacation with their family

Industry/Entity Type

It Company

Coding

Coded - Design and coding required

Number of Pages Required

5+ page

Colors
fffbf0
cadf82
fbf289
f6faec
fdf9cf
eaf2ce
fff3d1
fee18a
abd037

Requirements
Must have
• - Must be designed in Wordpress using the Velmora template I have provided or another suitable web template.
• - Must be Responsive Web Design so that the website adjusts to various screen sizes.

```html
<!DOCTYPE html>
<html lang="en">
<head>
<meta charset="utf-8">
<title>Tidal Otter – Cayman's Premier Adventure and Rental Company</title>
<link href="https://fonts.googleapis.com/css2?family=Roboto:wght@300;400;500;700&display=swap" rel="stylesheet">
<style>
:root{
  --page:#ece7dc;
  --ink:#1d1d1d;
  --text:#4a4a4a;
  --green:#abd037;
  --green-dark:#8fb320;
  --teal:#5cc4c4;
  --nav:#161616;
  --footer:#1e1e1e;
  --footer-bar:#121212;
  --muted:#9a9a9a;
  --white:#ffffff;
  --yellow:#fee18a;
}
*{box-sizing:border-box;margin:0;padding:0}
html,body{width:1200px;height:4401px;overflow:hidden}
body{background:var(--page);font-family:"Roboto",sans-serif;color:var(--text);position:relative}
.abs{position:absolute}
/* header */
.brand{left:0;width:1200px;top:30px;display:flex;flex-direction:column;align-items:center}
.brand-mark{display:flex;align-items:center;gap:14px}
.brand-dot{width:64px;height:64px;border-radius:50%;background:var(--teal)}
.brand-name{font-size:44px;font-weight:700;color:var(--ink);letter-spacing:1px}
.tagline{left:0;width:1200px;top:196px;text-align:center;color:var(--teal);font-size:15px;letter-spacing:1px;text-transform:uppercase}
.main-nav{left:0;top:240px;width:1200px;height:40px;background:var(--nav);display:flex;justify-content:center;align-items:center;gap:46px}
.main-nav a{color:var(--white);text-decoration:none;font-size:12px;font-weight:500;letter-spacing:.5px;text-transform:uppercase}
.hero{left:0;top:282px;width:1200px;height:428px;background:linear-gradient(180deg,#9fd2ef 0%,#c7e6f2 22%,#4fc6cf 30%,#24b4c0 60%,#4fcfd0 100%)}
/* features */
.features{left:160px;top:751px;width:880px;display:flex;justify-content:space-between}
.feature{width:270px;text-align:center}
.feature-photo{height:188px;box-shadow:0 2px 6px rgba(0,0,0,.25)}
.feature h3{margin-top:24px;font-size:14px;font-weight:700;color:var(--ink);text-transform:uppercase}
.feature p{margin-top:8px;font-size:12px;line-height:16px}
/* welcome */
.welcome{left:200px;top:1090px;width:800px;text-align:center}
.welcome h1{font-size:30px;font-weight:700;color:var(--ink);text-transform:uppercase}
.welcome p{margin-top:24px;font-size:12px;line-height:17px;padding:0 20px}
/* story rows */
.story{left:160px;width:880px;height:280px;display:flex;justify-content:space-between;align-items:flex-start}
.story.flip{flex-direction:row-reverse}
.story-text{width:340px;padding-top:24px}
.story.flip .story-text{width:360px;padding-left:20px}
.story-text h2{font-size:22px;font-weight:700;line-height:27px;color:var(--ink)}
.story-text h2 span{display:block;padding-left:24px}
.story-text p{margin-top:18px;font-size:12px;line-height:17px}
.story-photo{width:410px;height:280px;box-shadow:10px 10px 0 #222}
.btn{display:inline-flex;align-items:center;gap:8px;margin-top:30px;background:var(--green);color:var(--ink);font-size:12px;font-weight:700;height:40px;padding:0 20px;text-transform:uppercase}
.btn svg{width:14px;height:14px}
/* top picks */
.picks-title{left:0;width:1200px;top:3605px;text-align:center;font-size:28px;font-weight:700;color:var(--ink);text-transform:uppercase}
.picks{left:160px;top:3691px;width:880px;display:flex;justify-content:space-between}
.pick{width:205px;background:var(--white);box-shadow:0 2px 5px rgba(0,0,0,.2)}
.pick-photo{height:123px}
.pick-body{height:118px;text-align:center;padding-top:20px}
.pick h3{font-size:15px;font-weight:700;color:var(--ink);text-transform:uppercase}
.pick p{font-size:11px;margin-top:6px}
.pick .btn{margin-top:14px;height:24px;font-size:9px;padding:0 12px}
.pick .btn svg{width:10px;height:10px}
/* footer */
.site-footer{left:0;top:4005px;width:1200px;height:361px;background:var(--footer);color:var(--muted)}
.col{position:absolute;top:36px}
.col h4{color:var(--white);font-size:15px;font-weight:700;text-transform:uppercase;margin-bottom:18px}
.about{left:160px;width:230px;font-size:11px;line-height:15px}
.contact-line{margin-top:14px}
.contact-line b{display:flex;align-items:center;gap:6px;color:var(--white);font-size:12px;text-transform:uppercase}
.contact-line b svg{width:12px;height:12px}
.blog{left:446px;width:260px}
.post{display:flex;gap:12px;margin-bottom:14px}
.date{width:50px;height:56px;border:1px solid #444;text-align:center;color:var(--white);padding-top:4px}
.date strong{display:block;font-size:22px}
.date small{font-size:9px;text-transform:uppercase}
.post-info{font-size:10px;line-height:14px}
.post-info em{font-style:normal;color:var(--white);font-size:11px}
.form{left:754px;width:290px}
.field{height:34px;border:1px solid #3d3d3d;background:#262626;margin-bottom:10px;font-size:11px;padding:10px}
.field.tall{height:70px}
.submit{display:inline-block;background:var(--yellow);color:var(--ink);font-weight:700;font-size:12px;padding:10px 18px;text-transform:uppercase}
.footer-bar{left:0;top:4366px;width:1200px;height:35px;background:var(--footer-bar);display:flex;align-items:center;justify-content:space-between;padding:0 160px;font-size:11px;color:var(--muted)}
.dots{display:flex;gap:14px}
.dots i{width:10px;height:10px;border-radius:50%;background:#666;display:block}
</style>
</head>
<body>

<header>
  <div class="abs brand"><div class="brand-mark"><span class="brand-dot"></span><span class="brand-name">Tidal Otter</span></div></div>
  <p class="abs tagline">Cayman's premier adventure and rental company</p>
  <nav class="abs main-nav">
    <a href="#">Home</a><a href="#">Rental Gear</a><a href="#">Adventure Map</a><a href="#">Tours</a><a href="#">Photo Gallery</a><a href="#">Contact Us</a>
  </nav>
  <div class="abs hero" role="img" aria-label="Photo of turquoise Cayman sea with a colourful outrigger boat and the shoreline"></div>
</header>

<section class="abs features">
  <div class="feature">
    <div class="feature-photo" role="img" aria-label="Photo of two people paddling a kayak on clear water" style="background:linear-gradient(160deg,#6fcad6,#2fa6b5)"></div>
    <h3>Exploration</h3>
    <p>Rent everything you need to get outside and explore the island on your own terms. Snorkel the Kittiwake, check out the bioluminescence and much more with your own gear!</p>
  </div>
  <div class="feature">
    <div class="feature-photo" role="img" aria-label="Photo of a person relaxing on an inflatable lounger in the sea" style="background:linear-gradient(160deg,#7fd6d2,#27a9ae)"></div>
    <h3>Relaxation</h3>
    <p>We will come straight to your resort or condo and set everything up for you and your family to enjoy our kayaks and paddle boards on the beautiful calm waters off Seven Mile Beach.</p>
  </div>
  <div class="feature">
    <div class="feature-photo" role="img" aria-label="Placeholder photo for the education feature" style="background:#fafafa;border:1px solid #d8d8d8"></div>
    <h3>Education</h3>
    <p>We love sharing our knowledge on Cayman's history and the island's extraordinary marine life. We'll also teach you everything you need to find those secluded spots on your adventures.</p>
  </div>
</section>

<section class="abs welcome">
  <h1>Welcome to Tidal Otter!</h1>
  <p>We love having the freedom to explore when travelling and we bet you do too! We are Grand Cayman's premier rental company, offering everything you need to make the most of your vacation. Our website serves as a great starting point to help you prepare for your vacation here in Cayman. We feature a huge selection of adventures on our interactive map with tons of useful information, pictures and directions. Our adventure map is the perfect guide to all our great spots to check out here in Cayman.</p>
</section>

<svg width="0" height="0" style="position:absolute">
  <symbol id="arrow-circle" viewBox="0 0 14 14"><circle cx="7" cy="7" r="7" fill="#1d1d1d"/><path d="M5.5 4l3 3-3 3" stroke="#abd037" stroke-width="1.8" fill="none"/></symbol>
</svg>

<section class="abs story" style="top:1303px">
  <div class="story-text">
    <h2>Your one stop shop for all <span>the rentals you need here in Cayman!</span></h2>
    <p>We have a huge array of fun toys and equipment for you to enjoy. Whether it's for exploring or relaxing, we have all the equipment you need to make the most of your trip here in Cayman. Need something that we don't stock, just ask and we'll do everything we can to get you the gear you need!</p>
    <a class="btn" href="#">Read more <svg><use href="#arrow-circle"/></svg></a>
  </div>
  <div class="story-photo" role="img" aria-label="Aerial photo of kayaks and paddlers on turquoise water" style="background:linear-gradient(160deg,#56c6cf,#1f93a8)"></div>
</section>

<section class="abs story flip" style="top:1634px">
  <div class="story-text" style="padding-top:40px">
    <h2>Check out our <span>interactive map of Cayman!</span></h2>
    <p>You won't find any tourist traps on our map! We're all about getting off the beaten path and finding those unique spots and natural wonders to explore. Get our expert advice on which adventures are best for you and how to tackle them!</p>
    <a class="btn" href="#">Read more <svg><use href="#arrow-circle"/></svg></a>
  </div>
  <div class="story-photo" role="img" aria-label="Illustrated adventure map of Grand Cayman" style="background:linear-gradient(160deg,#8fd3ea,#63b9d6 60%,#b8d97a)"></div>
</section>

<section class="abs story" style="top:1960px">
  <div class="story-text">
    <h2>Enjoy <span>Complete freedom to explore</span></h2>
    <p>Inflatable kayaks have revolutionized the way kayak exploration is done in a way never before. Our kayaks give you the freedom to explore Cayman's most secluded locations and snorkel those hard to reach reefs. Our kayaks are light, comfortable and easy to use.</p>
    <a class="btn" href="#">Read more <svg><use href="#arrow-circle"/></svg></a>
  </div>
  <div class="story-photo" role="img" aria-label="Photo of two children in a blue inflatable kayak" style="background:linear-gradient(170deg,#9ad7ec,#43b8c9 55%,#2d8fb0)"></div>
</section>

<section class="abs story flip" style="top:2283px">
  <div class="story-text" style="padding-top:34px">
    <h2>There's no easier <span>way to get around the island</span></h2>
    <p>What better way is there to explore the island other than to rent a bike and go! Our mountain bikes are perfect for those interested on heading out on a full day adventure. If you're looking for something more casual, renting a cruiser is perfect to get around the Seven Mile Beach area. Use our map to help guide you to all our suggested locations to explore!</p>
    <a class="btn" href="#">Read more <svg><use href="#arrow-circle"/></svg></a>
  </div>
  <div class="story-photo" role="img" aria-label="Photo of two beach cruiser bicycles on the sand" style="background:linear-gradient(180deg,#7fc6e6,#bfe3ef 45%,#e9dcc2 60%,#d8c8a8)"></div>
</section>

<section class="abs story" style="top:2614px">
  <div class="story-text">
    <h2>We want to be your personal concierge and help you to plan out your trip!</h2>
    <p>When we come to deliver your equipment, we teach you everything you need to know about the island including the best hidden spots, best restaurants &amp; bars to eat &amp; drink and anything else you might be curious about. Please don't hesitate to contact us for any and all of your vacation questions. We are happy to help!</p>
    <a class="btn" href="#">Read more <svg><use href="#arrow-circle"/></svg></a>
  </div>
  <div class="story-photo" role="img" aria-label="Placeholder photo for the concierge service" style="background:#fafafa"></div>
</section>

<section class="abs story flip" style="top:2937px">
  <div class="story-text" style="padding-top:44px">
    <h2>Is it a boat? <span>is it a whale?... It's a Floatnest!</span></h2>
    <p>Easily one of the coolest inventions we've ever come across, the Floatnest is a hammock craft the whole family can enjoy together. Spend the day cruising along Seven Mile Beach in style as you bar hop with your clan. Better still, bring a cooler on board and put the kids to work paddling as you relax in your hammock on the crystal clear waters!</p>
    <a class="btn" href="#">Read more <svg><use href="#arrow-circle"/></svg></a>
  </div>
  <div class="story-photo" role="img" aria-label="Aerial photo of a floating hammock craft on green-blue water" style="background:linear-gradient(160deg,#4fbfb0,#2a9c8e)"></div>
</section>

<section class="abs story" style="top:3267px">
  <div class="story-text">
    <h2>A new way to Snorkel!</h2>
    <p>Our full face snorkel masks are easy to use, making them perfect for kids and beginners. You simply put the mask on and breath as you usually would. There's no need to get used to breathing from your mouth and you don't experience a sore jaw from having to hold the mouth piece in place. Just ask and we'll bring one along for you to try!</p>
    <a class="btn" href="#">Read more <svg><use href="#arrow-circle"/></svg></a>
  </div>
  <div class="story-photo" role="img" aria-label="Underwater photo of a snorkeller with a full face mask" style="background:linear-gradient(170deg,#7fcfe0,#3f9fc2)"></div>
</section>

<h2 class="abs picks-title">Our adventure top-picks</h2>
<section class="abs picks">
  <article class="pick">
    <div class="pick-photo" role="img" aria-label="Photo of glowing blue bioluminescent bay at night" style="background:linear-gradient(160deg,#0b2a5a,#1f6fc7)"></div>
    <div class="pick-body"><h3>Bio Bay</h3><p>Glowing waters after dark</p><a class="btn" href="#">Read more <svg><use href="#arrow-circle"/></svg></a></div>
  </article>
  <article class="pick">
    <div class="pick-photo" role="img" aria-label="Underwater photo of the Kittiwake shipwreck" style="background:linear-gradient(160deg,#5fb3c4,#236f8a)"></div>
    <div class="pick-body"><h3>Kittiwake</h3><p>Snorkel a sunken ship</p><a class="btn" href="#">Read more <svg><use href="#arrow-circle"/></svg></a></div>
  </article>
  <article class="pick">
    <div class="pick-photo" role="img" aria-label="Aerial photo of a small sandy cay in turquoise sea" style="background:linear-gradient(160deg,#6fd0d8,#2fa6b8)"></div>
    <div class="pick-body"><h3>Sand Cay Island</h3><p>A tiny island all yours</p><a class="btn" href="#">Read more <svg><use href="#arrow-circle"/></svg></a></div>
  </article>
  <article class="pick">
    <div class="pick-photo" role="img" aria-label="Photo of stingrays in shallow clear water" style="background:linear-gradient(160deg,#8fd9d8,#3bb3bd)"></div>
    <div class="pick-body"><h3>Stingray City</h3><p>Swim with gentle rays</p><a class="btn" href="#">Read more <svg><use href="#arrow-circle"/></svg></a></div>
  </article>
</section>

<footer class="abs site-footer">
  <div class="col about">
    <h4>About us</h4>
    <p>Local paddlers delivering kayaks, boards and snorkel gear to your door across Grand Cayman.</p>
    <div class="contact-line"><b><svg viewBox="0 0 12 12"><path d="M6 0a4 4 0 0 1 4 4c0 3-4 8-4 8S2 7 2 4a4 4 0 0 1 4-4z" fill="#fff"/><circle cx="6" cy="4" r="1.5" fill="#1e1e1e"/></svg>Address:</b>42 Harbour Drive, George Town, KY1-1102</div>
    <div class="contact-line"><b><svg viewBox="0 0 12 12"><path d="M2 1l2.5 0 1 3-1.5 1a7 7 0 0 0 3 3l1-1.5 3 1V10a1 1 0 0 1-1 1C5 11 1 7 1 2a1 1 0 0 1 1-1z" fill="#fff"/></svg>Telephone:</b>+1 (345) 555 0192</div>
    <div class="contact-line"><b><svg viewBox="0 0 12 12"><rect x="0" y="2" width="12" height="8" fill="#fff"/><path d="M0 2l6 4 6-4" stroke="#1e1e1e" fill="none"/></svg>Email:</b>hello@tidalotterco.com</div>
  </div>
  <div class="col blog">
    <h4>Latest blog</h4>
    <div class="post"><div class="date"><strong>01</strong><small>Jun</small></div><div class="post-info"><em>Best reefs for first-time snorkellers</em><br>Jun 01, 2017 · 9:00 am<br>George Town</div></div>
    <div class="post"><div class="date"><strong>01</strong><small>Jun</small></div><div class="post-info"><em>Paddling the mangroves at sunrise</em><br>Jun 01, 2017 · 9:00 am<br>George Town</div></div>
    <div class="post"><div class="date"><strong>01</strong><small>Jun</small></div><div class="post-info"><em>Packing list for a beach day</em><br>Jun 01, 2017 · 9:00 am<br>George Town</div></div>
  </div>
  <div class="col form">
    <h4>Contact form</h4>
    <div class="field">Your name</div>
    <div class="field">Your email</div>
    <div class="field tall">Your message</div>
    <span class="submit">Submit</span>
  </div>
</footer>
<div class="abs footer-bar"><span>© 2017 tidalotterco.com. All Right Reserved</span><span class="dots"><i></i><i></i><i></i><i></i></span></div>

</body>
</html>
```